Systems and Technology Consultants - Website

Design & Build a website for a new company which operates in the Systems and Technology space for Transportation, Government and Commercial sectors.

Overall design should be minimalist in nature.
Should also have a feed that provides news and event updates on the main page.
Logo has already been awarded and should be incorporated into the site.

We like the overall layout, functionality and simplicity of the below sites. Submitted designs could be similar to or a combination of the aspects on these sites, or perhaps a whole different concept - we are open to new ideas.
Norvique.com
Teblo.it

Update 1 Dated 27 May 2014

All I am moving away from the Teblo.it website and would like it to be more aligned with Norvique.com not only in layout but in functionality. I will be extending the deadline of this design brief for two weeks to incorporate additional requirements and will add addtional funding to the project.

Apologies for not having more information available to provide but with so many submissions its getting confusing.

Thanks Derek

Please note that the brief has been updated and the deadline has been extended.

Important: We will need two language versions of the website, English and Arabic; the website is hosted on HostPelican

Hello All, Thank you for your submissions. We have narrowed it down to the final 6 designers and I just wanted to take a moment and provide a bit of feedback regarding the concepts that we like and the modifications we are looking for. First, let me mention some of the design functions we like. - At the top of the homepage we really like the "region" or "language" tab so that the website can be viewed in both English and Arabic. - We like the homepage to have clear color variation so that the different sections of the homepage are distinct. Additionally, we like the bottom portion of the homepage to be in red. We feel that draws attention to our contact information. Again, we would like the colors to integrate black, gray-scale, red, etc. - Having a search tab at the top of the home page, or integrated into the main image, so that the site is easy to navigate. - We especially like the main image to have the scrolling tabs at the bottom so it is easy to browse the services offered (Consultancy, Solutions Architecture, Masters Systems Integration, Independent Design Review). - In regards to the services offered tab we really like the idea that a few people presented that have the outside of our logo with an icon in the middle of consultancy, solutions, etc., etc. Secondly, as mentioned in our brief we really enjoy the design of norvique site. Specially, we enjoy the strong iconic images they use, the way the tabs at the top scroll easily, and contact us page that generates an email. Lastly, I've included some photos of the concept we have been working on. What we are trying to demonstrate is how our company offers a range of services that are essentially linked together. We provide individual services that when combined present the full service package. We would like this concept to be integrated into the over concept of our website. Please feel free to ask for clarification of any of the above points or contact us if you have any additional questions. We appreciate all of your hard work and are very excited to see the updated designs. Best, Marta Vennick Quelbrant Senior Program Manager marta.vennick@quelbrant-example.com

Industry/Entity Type

Government

Font styles to use
Serif
Sans Serif

Requirements
Must have
• Must work on/adapt to various/mobile devices (responsive)
Must be simple and straightforward
Colors should be in line/matching with logo
2 language versions: English and Arabic (no Thai)
Services should be the first group/row of items after/below the main image
Note: the website will be hosted by hostpelican
Nice to have
• Submit feedback form
What's New section
The banner at the bottom of the site should not be too large; we would like a narrow one more
It would be nice if the header/top banner (with Home, About, etc. tabs) could stay in place as you scroll down (like Norvique and Chatterloop)
We will likely only use one image with a Company slogan on the Home page rather than a carousel of images to rotate through
Should not have
• This is the existing website: http://www.quelbrant-example.org
We do not like the animation, the way the banner icons/titles bounce
Not simple enough, we don't like the functionality or how pages load so slowly
We do not like the logo centered - it should be at the left
The banner and its tabs should not be towards the right, we would like them to be centered, to go all the way across and to be below the logo

```html
<!DOCTYPE html>
<html lang="en">
<head>
<meta charset="utf-8">
<title>Quelbrant</title>
<link rel="stylesheet" href="https://fonts.googleapis.com/css2?family=Open+Sans:ital,wght@0,300;0,400;0,600;1,400&family=Arimo:ital,wght@0,400;0,700;1,400&display=swap">
<style>
:root{
  --red:#fe0000;
  --red-dark:#c80000;
  --ink:#222;
  --text:#444;
  --grey:#8a8a8a;
  --rule:#d9d9d9;
  --footer:#3a3a3a;
  --footer-text:#e6e6e6;
  --white:#fff;
}
*{margin:0;padding:0;box-sizing:border-box}
html,body{width:917px;height:1200px;overflow:hidden;background:var(--white)}
body{position:relative;font-family:"Arimo",Arial,sans-serif;color:var(--text)}
.abs{position:absolute}
.site-header{position:absolute;left:0;top:0;width:917px;height:67px;background:var(--white);border-bottom:1px solid #eee}
.brand{position:absolute;left:128px;top:22px;display:flex;align-items:center;gap:6px;font-family:"Open Sans",sans-serif;font-weight:600;font-size:14px;letter-spacing:2px;color:var(--red)}
.brand-mark{width:10px;height:10px;background:var(--red)}
.main-nav a{position:absolute;top:29px;font-size:10.5px;color:#555;text-decoration:none}
.hero{position:absolute;left:0;top:67px;width:917px;height:322px;background:linear-gradient(100deg,#e9ecee 0%,#cfd3d5 35%,#a9aeb0 60%,#e6e7e6 85%,#d7d9da 100%)}
.hero-arrow{position:absolute;top:146px;width:34px;height:34px;border:2px solid rgba(255,255,255,.75);border-radius:50%}
.title{position:absolute;left:0;width:917px;text-align:center;font-family:"Open Sans",sans-serif;font-weight:300;color:var(--ink)}
.lead{position:absolute;left:140px;width:637px;text-align:center;color:var(--text)}
.divider{position:absolute;left:131px;top:515px;width:655px;height:1px;background:var(--rule)}
.service{position:absolute;top:651px;width:140px;text-align:center}
.service-icon{display:block;margin:0 auto;width:80px;height:80px}
.service-name{margin-top:10px;font-family:"Open Sans",sans-serif;font-size:12px;color:var(--ink)}
.service-desc{margin-top:8px;font-size:7.6px;line-height:15.7px;color:var(--text)}
.carousel-arrow{position:absolute;top:688px}
.news{position:absolute;left:0;top:850px;width:917px;height:276px;background:var(--red);color:var(--white)}
.news-photo{position:absolute;left:131px;top:41px;width:207px;height:195px;border:5px solid var(--red-dark);background:linear-gradient(120deg,#eef0ee,#c9cdcc 55%,#8d9190)}
.news-title{position:absolute;left:370px;top:40px;font-family:"Open Sans",sans-serif;font-weight:300;font-size:26px}
.news-pager{position:absolute;left:723px;top:46px;display:flex;gap:3px}
.news-pager span{width:16px;height:16px;background:var(--red-dark);display:flex;align-items:center;justify-content:center}
.news-headline{position:absolute;left:370px;top:80px;font-family:"Open Sans",sans-serif;font-weight:300;font-size:17px}
.news-date{position:absolute;left:373px;top:110px;font-size:9px;font-style:italic}
.news-body{position:absolute;left:373px;top:129px;width:390px;font-size:7.8px;line-height:15.8px}
.read-more{position:absolute;left:374px;top:204px;width:92px;height:25px;background:var(--red-dark);color:var(--white);font-size:8px;display:flex;align-items:center;justify-content:center;gap:4px}
.site-footer{position:absolute;left:0;top:1126px;width:917px;height:74px;background:var(--footer);color:var(--footer-text)}
.footer-nav a{position:absolute;top:21px;font-size:8px;color:var(--footer-text);text-decoration:none}
.copyright{position:absolute;left:135px;top:43px;font-size:8px}
.social{position:absolute;top:27px;width:20px;height:20px;border-radius:50%;background:#8c8c8c}
</style>
</head>
<body>

<header class="site-header">
  <div class="brand"><span class="brand-mark"></span>QUELBRANT</div>
  <nav class="main-nav">
    <a style="left:303px">Home</a>
    <a style="left:373px">Business Units</a>
    <a style="left:482px">Services</a>
    <a style="left:563px">About Us</a>
    <a style="left:647px">Locations</a>
    <a style="left:733px">Contact Us</a>
  </nav>
</header>

<section class="hero" role="img" aria-label="Photo of a smiling business team meeting around a laptop in a bright office">
  <span class="hero-arrow" style="left:63px"></span>
  <span class="hero-arrow" style="left:823px"></span>
</section>

<h1 class="title" style="top:416px;font-size:27px">Welcome to Quelbrant</h1>
<p class="lead" style="top:460px;font-size:9.6px;line-height:17px">quelbrant specializes in delivering quality professional services and technical projects that support larger business goals.&nbsp; systems are tools that support a greater business function and need. we understand that most technical projects are conceptualized to support...</p>

<div class="divider"></div>

<h2 class="title" style="top:535px;font-size:27px">Services Offered</h2>
<p class="lead" style="left:140px;width:637px;top:579px;font-size:7.7px;line-height:16px">quelbrant specializes in delivering quality professional services and technical projects that support larger business goals.&nbsp; systems are tools that support a greater business function and need. we understand that most technical projects are conceptualized to support a larger vision with actual business goals in mind and ensure that all of our professional and certified expertise is included in our professional services to meet those goals.</p>

<svg class="carousel-arrow" style="left:120px" width="10" height="22" viewBox="0 0 10 22"><path d="M9 1 L1 11 L9 21" fill="none" stroke="#999" stroke-width="1"/></svg>
<svg class="carousel-arrow" style="left:790px" width="10" height="22" viewBox="0 0 10 22"><path d="M1 1 L9 11 L1 21" fill="none" stroke="#999" stroke-width="1"/></svg>

<div class="service" style="left:132px">
  <svg class="service-icon" viewBox="0 0 80 80"><circle cx="40" cy="40" r="40" fill="#fe0000"/>
    <g fill="#fff"><circle cx="29" cy="29" r="3.5"/><rect x="25" y="34" width="8" height="14" rx="2"/><rect x="26" y="48" width="2.5" height="10"/><rect x="30" y="48" width="2.5" height="10"/>
    <circle cx="52" cy="29" r="3.5"/><rect x="48" y="34" width="8" height="14" rx="2"/><rect x="49" y="48" width="2.5" height="10"/><rect x="53" y="48" width="2.5" height="10"/>
    <rect x="39" y="40" width="3" height="1"/><rect x="40" y="39" width="1" height="3"/></g></svg>
  <div class="service-name">Consulting</div>
  <p class="service-desc">quelbrant specializes in delivering quality professional services and technical projects...</p>
</div>

<div class="service" style="left:307px">
  <svg class="service-icon" viewBox="0 0 80 80"><circle cx="40" cy="40" r="40" fill="#8a8a8a"/>
    <g fill="#fff" transform="translate(40 40)">
      <rect x="-4" y="-21" width="8" height="9" transform="rotate(0)"/><rect x="-4" y="-21" width="8" height="9" transform="rotate(45)"/><rect x="-4" y="-21" width="8" height="9" transform="rotate(90)"/><rect x="-4" y="-21" width="8" height="9" transform="rotate(135)"/><rect x="-4" y="-21" width="8" height="9" transform="rotate(180)"/><rect x="-4" y="-21" width="8" height="9" transform="rotate(225)"/><rect x="-4" y="-21" width="8" height="9" transform="rotate(270)"/><rect x="-4" y="-21" width="8" height="9" transform="rotate(315)"/>
      <circle r="15"/></g><circle cx="40" cy="40" r="7" fill="#8a8a8a"/></svg>
  <div class="service-name">Engineering</div>
  <p class="service-desc">quelbrant specializes in delivering quality professional services and technical projects...</p>
</div>

<div class="service" style="left:477px">
  <svg class="service-icon" viewBox="0 0 80 80"><circle cx="40" cy="40" r="40" fill="#8a8a8a"/>
    <g fill="#fff"><circle cx="34" cy="23" r="4"/><path d="M30 29 L37 29 L42 42 L38 43 L36 38 L32 45 L28 55 L24 54 L28 43 Z"/><path d="M40 55 L50 40 L60 55 Z"/></g></svg>
  <div class="service-name">Construction</div>
  <p class="service-desc">quelbrant specializes in delivering quality professional services and technical projects...</p>
</div>

<div class="service" style="left:646px">
  <svg class="service-icon" viewBox="0 0 80 80"><circle cx="40" cy="40" r="40" fill="#8a8a8a"/>
    <g fill="#fff"><circle cx="44" cy="29" r="6"/><path d="M22 43 L33 41 L45 43 Q48 45 45 47 L36 47 L46 48 L58 40 Q61 40 59 44 L47 53 L33 54 L22 51 Z"/></g>
    <circle cx="44" cy="29" r="2.5" fill="#8a8a8a"/></svg>
  <div class="service-name">Maintenance</div>
  <p class="service-desc">quelbrant specializes in delivering quality professional services and technical projects...</p>
</div>

<section class="news">
  <div class="news-photo" role="img" aria-label="Photo of colleagues working together at a laptop"></div>
  <h2 class="news-title">News &amp; Events</h2>
  <div class="news-pager">
    <span><svg width="6" height="8" viewBox="0 0 6 8"><path d="M5 0.5 L1 4 L5 7.5" fill="none" stroke="#fff"/></svg></span>
    <span><svg width="6" height="8" viewBox="0 0 6 8"><path d="M1 0.5 L5 4 L1 7.5" fill="none" stroke="#fff"/></svg></span>
  </div>
  <h3 class="news-headline">Systems and Technology space for Transportation</h3>
  <p class="news-date">Posted on 27 march 2014</p>
  <p class="news-body">quelbrant specializes in delivering quality professional services and technical projects that support larger business goals.&nbsp; systems are tools that support a greater business function and need. we understand that most technical projects are conceptualized to support a larger vision with actual business goals.we understand that most technical projects are conceptualized to support a larger...</p>
  <a class="read-more">READ MORE <svg width="9" height="7" viewBox="0 0 9 7"><path d="M1 0.5 L4 3.5 L1 6.5 M5 0.5 L8 3.5 L5 6.5" fill="none" stroke="#fff" stroke-width="1.2"/></svg></a>
</section>

<footer class="site-footer">
  <nav class="footer-nav">
    <a style="left:135px">Home</a>
    <a style="left:190px">Business Units</a>
    <a style="left:278px">Services</a>
    <a style="left:342px">About Us</a>
    <a style="left:410px">Locations</a>
    <a style="left:478px">Contact Us</a>
  </nav>
  <p class="copyright">Copyright. 2014 Quelbrant All rights reserved.</p>
  <span class="social" style="left:656px"></span>
  <span class="social" style="left:683px"></span>
  <span class="social" style="left:710px"></span>
  <span class="social" style="left:737px"></span>
  <span class="social" style="left:764px"></span>
</footer>

</body>
</html>
```